Boutique custom software development company needs new business card

Our nearly 20 year old custom software development company would like to better include the fact that we are now providing Bitcoin services. These new services are B2B include education (how to acquire and securely hold Bitcoin) and integrating Bitcoin payments into existing ecommerce sites or other existing systems. Please keep the card clean and simple. Attached is our current design and some other files. vextorial.com

Target Market(s)

businesses owners interested in long term relationship

Industry/Entity Type

Custom software development and Bitcoin

Contact Information for Business Card

Dale Parker, dale@vextorial.com, vextorial.com, (888) 555-VXTRL

Font styles to use
Other font styles liked:
• monospace

Requirements
Must have
• double-sided
Nice to have
• clean and simple
Should not have
• physical address

```html
<!DOCTYPE html>
<html lang="en">
<head>
<meta charset="utf-8">
<title>Vextorial Business Card</title>
<link rel="stylesheet" href="https://fonts.googleapis.com/css2?family=Lato:wght@400&family=Montserrat:wght@400;700;800&family=Roboto+Mono:wght@500&display=swap">
<style>
  :root {
    --brand-blue: #3f72b9;
    --brand-orange: #f07f22;
    --card-white: #ffffff;
    --ink: #333333;
    --backdrop: #e9e5df;
  }
  * { margin: 0; padding: 0; box-sizing: border-box; }
  html, body { width: 900px; height: 1200px; overflow: hidden; }
  body {
    position: relative;
    background: var(--backdrop);
    font-family: "Montserrat", Arial, sans-serif;
  }
  .card {
    position: absolute;
    left: 80px;
    width: 742px;
    height: 440px;
    border-radius: 34px;
    box-shadow: 0 6px 16px rgba(0,0,0,0.25);
    overflow: hidden;
  }
  .card--front { top: 132px; background: var(--card-white); }
  .card--back { top: 640px; height: 438px; background: var(--brand-blue); }

  .brand-square {
    position: absolute;
    left: 42px; top: 36px;
    width: 124px; height: 124px;
    background: var(--brand-blue);
  }
  .brand-name {
    position: absolute;
    font-family: "Montserrat", Arial, sans-serif;
    font-weight: 800;
    line-height: 1;
    letter-spacing: -1px;
    white-space: nowrap;
  }
  .card--front .brand-name {
    left: 200px; top: 58px;
    font-size: 53px;
    color: var(--brand-blue);
  }
  .tagline {
    position: absolute;
    font-family: "Lato", Arial, sans-serif;
    font-weight: 400;
    letter-spacing: -0.3px;
    white-space: nowrap;
  }
  .card--front .tagline {
    left: 212px; top: 124px;
    font-size: 21px;
    color: var(--brand-blue);
  }
  .service-line {
    position: absolute;
    font-family: "Roboto Mono", "Courier New", monospace;
    font-weight: 500;
    white-space: nowrap;
  }
  .card--front .service-line {
    left: 213px; top: 158px;
    font-size: 14px;
    color: var(--brand-orange);
  }

  .person-name {
    position: absolute;
    left: 42px; top: 264px;
    font-size: 26px;
    font-weight: 700;
    color: var(--brand-blue);
  }
  .person-role {
    position: absolute;
    left: 43px; top: 297px;
    font-size: 16px;
    color: var(--ink);
  }
  .divider {
    position: absolute;
    left: 45px; top: 329px;
    width: 652px; height: 2px;
    background: var(--brand-blue);
  }
  .contact-list {
    position: absolute;
    left: 43px; top: 342px;
    list-style: none;
  }
  .contact-item {
    display: flex;
    align-items: center;
    height: 22.5px;
    font-size: 16px;
    color: var(--ink);
  }
  .contact-icon {
    width: 13px; height: 13px;
    margin-right: 11px;
    fill: var(--brand-blue);
  }

  .card--back .brand-name {
    left: 0; right: 18px; top: 142px;
    text-align: center;
    font-size: 92px;
    color: var(--card-white);
  }
  .card--back .tagline {
    left: 0; right: 18px; top: 258px;
    text-align: center;
    font-size: 37px;
    color: var(--card-white);
  }
  .card--back .service-line {
    left: 0; right: 18px; top: 322px;
    text-align: center;
    font-size: 19px;
    color: var(--brand-orange);
  }
</style>
</head>
<body>
  <section class="card card--front" aria-label="Card front">
    <div class="brand-square"></div>
    <div class="brand-name">VEXTORIAL</div>
    <div class="tagline">developer of custom applications</div>
    <div class="service-line">+ Bitcoin education &amp; payment integration</div>

    <div class="person-name">Dale Parker</div>
    <div class="person-role">Owner</div>
    <div class="divider"></div>

    <ul class="contact-list">
      <li class="contact-item">
        <svg class="contact-icon" viewBox="0 0 16 16" aria-hidden="true"><path d="M2 6c0-2 3-4 6-4s6 2 6 4v1h-3V5.5c-1-.6-5-.6-6 0V7H2zM4 8h8l2 5v1H2v-1zM8 9.5a1.5 1.5 0 100 3 1.5 1.5 0 000-3z"/></svg>
        (888) 555-VXTRL
      </li>
      <li class="contact-item">
        <svg class="contact-icon" viewBox="0 0 16 16" aria-hidden="true"><path d="M1 3h14v10H1zM2.5 4.5v.4L8 9l5.5-4.1v-.4z"/></svg>
        dale@vextorial.com
      </li>
      <li class="contact-item">
        <svg class="contact-icon" viewBox="0 0 16 16" aria-hidden="true"><circle cx="8" cy="8" r="7"/><path d="M4 5c1 0 2 1 2 2s1 1 1 2-1 2 0 3l-1 1C4 11 3 8 4 5zM9 3c1 1 3 1 3 3s-2 1-2 3 1 2 2 2" fill="#fff"/></svg>
        www.vextorial.com
      </li>
    </ul>
  </section>

  <section class="card card--back" aria-label="Card back">
    <div class="brand-name">VEXTORIAL</div>
    <div class="tagline">developer of custom applications</div>
    <div class="service-line">custom software · Bitcoin services for business</div>
  </section>
</body>
</html>
```